Boutique town planning business needs a Business Card design

We need a business card design for a new company called The Zoning Bridgeway. We provide town planning and urban design services to government, business and community groups. We would like to see the designs use the colours in the logo (blue, deep red, green and amber), plenty of white and including black and grey in the writing. The final design should communicate collaboration, creativity and professionalism and that we are approachable.

Industry/Entity Type

Town

```html
<!DOCTYPE html>
<html lang="en">
<head>
<meta charset="utf-8">
<title>The Zoning Bridgeway — Business Card</title>
<link rel="stylesheet" href="https://fonts.googleapis.com/css2?family=Roboto+Condensed:wght@400;700&family=Abel&display=swap">
<style>
  :root {
    --stage: #e4e4e4;
    --card: #ffffff;
    --card-back: #f7f7f7;
    --ink: #222222;
    --grey: #6b6b6b;
    --blue: #1e8fd2;
    --red: #b5332e;
    --green: #2f9a46;
    --amber: #ef7d22;
    --icon-red: #c0322b;
    --faint: #ececec;
  }
  * { box-sizing: border-box; margin: 0; padding: 0; }
  html, body {
    width: 1200px; height: 675px; overflow: hidden;
    background: var(--stage);
  }
  .stage {
    width: 1200px; height: 675px;
    display: flex; align-items: center; justify-content: center; gap: 50px;
  }
  .card {
    position: relative;
    width: 540px; height: 330px;
    background: var(--card);
    box-shadow: 0 10px 24px rgba(0,0,0,0.14);
    overflow: hidden;
  }
  .card--back { background: var(--card-back); }

  .card__watermark {
    position: absolute;
    width: 380px; height: 380px;
    border-radius: 50%;
    border: 26px solid var(--faint);
  }
  .card--front .card__watermark { right: -150px; top: -150px; }
  .card--back .card__watermark { left: 40px; top: 120px; }

  .brand {
    position: absolute;
    display: flex; align-items: center; gap: 12px;
  }
  .brand__dot {
    flex: none;
    border-radius: 50%;
    background: var(--blue);
  }
  .brand__name {
    font-family: "Roboto Condensed", sans-serif;
    font-weight: 700;
    color: var(--ink);
    line-height: 1;
    white-space: nowrap;
  }
  .card--front .brand { left: 50%; top: 50%; transform: translate(-50%, -50%); }
  .card--front .brand__dot { width: 70px; height: 70px; }
  .card--front .brand__name { font-size: 34px; }

  .card--back .brand { left: 32px; top: 168px; gap: 9px; }
  .card--back .brand__dot { width: 42px; height: 42px; }
  .card--back .brand__name { font-size: 21px; }

  .person {
    position: absolute; right: 34px; top: 30px;
    text-align: right;
    font-family: "Roboto Condensed", sans-serif;
  }
  .person__name { font-size: 17px; font-weight: 700; color: var(--ink); }
  .person__credentials { font-size: 10px; color: var(--grey); margin-top: 6px; }
  .person__role { font-size: 10px; color: var(--grey); margin-top: 2px; }

  .contacts {
    position: absolute; right: 30px; top: 140px;
    list-style: none;
    font-family: "Abel", sans-serif;
    font-size: 15px; color: var(--ink);
  }
  .contacts__item {
    display: flex; align-items: center; justify-content: flex-end; gap: 10px;
    height: 25px;
  }
  .contacts__icon { width: 15px; height: 15px; flex: none; fill: var(--icon-red); }
</style>
</head>
<body>
<main class="stage">
  <section class="card card--front" aria-label="Card front">
    <div class="card__watermark" aria-hidden="true"></div>
    <div class="brand">
      <span class="brand__dot" aria-hidden="true"></span>
      <span class="brand__name">The Zoning Bridgeway</span>
    </div>
  </section>

  <section class="card card--back" aria-label="Card back">
    <div class="card__watermark" aria-hidden="true"></div>
    <div class="person">
      <p class="person__name">Marguerite Holloway</p>
      <p class="person__credentials">BPD (Urban Planning), GDipPD, MPIA, VPELA</p>
      <p class="person__role">Director</p>
    </div>
    <div class="brand">
      <span class="brand__dot" aria-hidden="true"></span>
      <span class="brand__name">The Zoning Bridgeway</span>
    </div>
    <ul class="contacts">
      <li class="contacts__item">0412 386 905
        <svg class="contacts__icon" viewBox="0 0 16 16" aria-hidden="true"><path d="M1 6c0-2 3-4 7-4s7 2 7 4v1h-3V5.5C11 5 9.5 4.8 8 4.8S5 5 4 5.5V7H1z"/><rect x="3" y="8" width="10" height="6" rx="1"/></svg>
      </li>
      <li class="contacts__item">hello@zoningbridgeway.com.au
        <svg class="contacts__icon" viewBox="0 0 16 16" aria-hidden="true"><path d="M1 3h14v10H1z M2 4l6 5 6-5" fill="var(--icon-red)" stroke="#fff" stroke-width="1"/></svg>
      </li>
      <li class="contacts__item">www.zoningbridgeway.com.au
        <svg class="contacts__icon" viewBox="0 0 16 16" aria-hidden="true"><circle cx="8" cy="8" r="7"/><path d="M1 8h14M8 1v14M3 4h10M3 12h10" stroke="#fff" stroke-width="1" fill="none"/><ellipse cx="8" cy="8" rx="3" ry="7" stroke="#fff" stroke-width="1" fill="none"/></svg>
      </li>
      <li class="contacts__item">ABN 51824730916
        <svg class="contacts__icon" viewBox="0 0 16 16" aria-hidden="true"><path d="M5 1h2l-.6 4h3L10 1h2l-.6 4H14v2h-2.9l-.4 3H14v2h-3.6L10 15H8l.4-3h-3L5 15H3l.4-3H1v-2h2.7l.4-3H1V5h3.4zm1.1 6l-.4 3h3l.4-3z"/></svg>
      </li>
    </ul>
  </section>
</main>
</body>
</html>
```